Orvane Thinner Logo and Packaging Design

We are seeking a striking and professional logo and packaging design for our new product line, Orvane Thinner. This logo will be used on the packaging for three different sizes of half-transparent carboys: 1L, 4L, and 20L. Orvane Thinner is a high-quality solvent brand known for its excellent solvency, fast-drying properties, and pleasant smell. The logo should feature an eagle motif to symbolize power and precision, and our slogan, "FLY WITH QUALITY." The design should be suitable for placement on hardware store and warehouse shelves. Additionally, we need the designer to create an eagle logo to accompany the packaging.

Packaging Dimensions:
1L Carboy:
Front: 71mm height x 142mm width
Side: 71mm height x 73mm width
4L Carboy:
Front: 160mm height x 170mm width
Side: 160mm height x 120mm width
20L Carboy:
Front: 245mm height x 190mm width
Side: 215mm height x 190mm width
Front Label Requirements:

Product Name: Thinner QXR
Volume: 20L
Precautionary Statements:
Keep Away from Sources of ignition - No Smoking
Avoid Contact with Eyes
Do Not Empty into Drains or Sewers
Take Precautionary Measures Against Static Discharge
Hazard Statements:
Flammable Liquid and Vapor
May be fatal if swallowed or enters Airways
Causes Skin Irritation
Causes Serious Eye Irritation
Causes Damage to Organs if Prolonged or Repeated Exposure
Hazard Pictograms: (Include relevant hazard symbols)
Design Requirements:

Logo: Eagle motif (to be designed by the designer)
Slogan: FLY WITH QUALITY
Color Scheme: Designer to recommend (should be striking and professional for retail display)

Please see my latest picture. Kindly note the packaging is in Plastic Carboy (not in metal tin as per PS).

Eagle to be more majestic and bigger (as if soaring in the sky).
Singapore landscape as background to have Singapore identity such as KTR, Corvale wheel, terrace at the cove etc.

Eagle to be more majestic and bigger, wings to spread wide.
We not want it to be of photo style, but more on a cartoon style. Please see my latest file uploaded.

Target Market(s)

Our target market includes painting companies, construction companies, direct household consumers, and industrial users who require high-quality solvents for various applications.

Industry/Entity Type

Chemical, spray paint and painting, household, industrial

Requirements
Must have
• Professional and Striking Design: Eye-catching and professional packaging for retail shelves. Eagle Logo: A strong, precise eagle logo. Slogan: "FLY WITH QUALITY" prominently displayed. Clear Precautionary and Hazard Statements: Important safety information and pictograms. Volume Indication: Clearly marked (e.g., 1L, 4L, 20L). Eagle to be more majestic and bigger (as if soaring in the sky). Singapore landscape as background to have Singapore identity such as KTR, Corvale wheel, terrace at the cove etc.
Nice to have
• Color Scheme Recommendations: Suggestions for a professional, striking color scheme. Versatility: Design elements adaptable across different sizes of packaging. Environmentally Friendly Elements: Indications of sustainability or eco-friendliness in the design.
Should not have
• Overly Complex Designs: Avoid cluttered or overly intricate designs that detract from readability. Inconsistent Branding: Ensure all elements are cohesive and align with the brand identity.

```html
<!DOCTYPE html>
<html lang="en">
<head>
<meta charset="utf-8">
<title>Orvane Thinner – Label Range</title>
<link rel="stylesheet" href="https://fonts.googleapis.com/css2?family=Montserrat:wght@400;600;700;800;900&display=swap">
<style>
  :root {
    --stage-grey: #bdbbbc;
    --stage-light: #e6e6e6;
    --ink: #0d0d0d;
    --white: #ffffff;
    --green-a: #35ad5b;
    --green-b: #24aeae;
    --sunset-a: #e9ad46;
    --sunset-b: #ef7a8c;
    --dusk-a: #a07fc0;
    --dusk-b: #4c9cdc;
    --eco-green: #2e9e4a;
    --eco-navy: #2c3a7c;
    --eco-plum: #3a1f2c;
  }
  * { margin: 0; padding: 0; box-sizing: border-box; }
  html, body { width: 1200px; height: 569px; overflow: hidden; }
  body { position: relative; font-family: "Montserrat", sans-serif; background: var(--stage-light); }
  .stage-main { position: absolute; left: 0; top: 0; width: 783px; height: 569px; background: var(--stage-grey); }
  .stage-side { position: absolute; left: 783px; top: 0; width: 417px; height: 569px; background: var(--stage-light); }
  .label { position: absolute; display: block; }
  .label--20l { left: 74px; top: 88px; width: 314px; height: 406px; }
  .label--4l { left: 425px; top: 227px; width: 284px; height: 266px; }
  .label--1l { left: 425px; top: 88px; width: 236px; height: 117px; }
  .label--20l-side { left: 880px; top: 168px; width: 226px; height: 291px; }
  .brand { font-weight: 800; fill: var(--ink); }
  .product { font-weight: 900; fill: var(--ink); }
  .slogan { font-weight: 900; fill: var(--white); }
  .volume { font-weight: 800; fill: var(--white); }
  .safety { font-weight: 500; fill: var(--ink); }
  .safety-head { font-weight: 800; fill: var(--white); }
  .hazard-frame { fill: none; stroke: var(--ink); stroke-width: 2; }
  .hazard-glyph { fill: var(--ink); }
  .defs { position: absolute; width: 0; height: 0; }
</style>
</head>
<body>
<svg class="defs" aria-hidden="true">
  <defs>
    <linearGradient id="grad-green" x1="0" y1="0" x2="1" y2="1">
      <stop offset="0" stop-color="var(--green-a)"/>
      <stop offset="1" stop-color="var(--green-b)"/>
    </linearGradient>
    <linearGradient id="grad-sunset" x1="0" y1="0" x2="1" y2="0.4">
      <stop offset="0" stop-color="var(--sunset-a)"/>
      <stop offset="1" stop-color="var(--sunset-b)"/>
    </linearGradient>
    <linearGradient id="grad-dusk" x1="0" y1="0" x2="1" y2="0.5">
      <stop offset="0" stop-color="var(--dusk-a)"/>
      <stop offset="1" stop-color="var(--dusk-b)"/>
    </linearGradient>
    <linearGradient id="grad-eagle-art" x1="0" y1="0" x2="1" y2="1">
      <stop offset="0" stop-color="#ffffff" stop-opacity="0.45"/>
      <stop offset="1" stop-color="#ffffff" stop-opacity="0.15"/>
    </linearGradient>

    <symbol id="icon-flame" viewBox="-10 -10 20 20">
      <rect class="hazard-frame" x="-7" y="-7" width="14" height="14" transform="rotate(45)" stroke-width="1.4"/>
      <path class="hazard-glyph" d="M0 -5 C2 -2 3.5 0 3 2.5 C2.6 4.4 1.4 5 0 5 C-1.4 5 -2.8 4.2 -3 2.4 C-3.2 0.6 -1.8 -0.6 -1.2 -2 C-0.8 -0.6 -0.2 0 0.4 0.4 C0.6 -1.6 0.4 -3.2 0 -5 Z"/>
    </symbol>
    <symbol id="icon-exclaim" viewBox="-10 -10 20 20">
      <rect class="hazard-frame" x="-7" y="-7" width="14" height="14" transform="rotate(45)" stroke-width="1.4"/>
      <rect class="hazard-glyph" x="-1" y="-5" width="2" height="6.5" rx="0.6"/>
      <circle class="hazard-glyph" cx="0" cy="3.6" r="1.1"/>
    </symbol>
    <symbol id="icon-health" viewBox="-10 -10 20 20">
      <rect class="hazard-frame" x="-7" y="-7" width="14" height="14" transform="rotate(45)" stroke-width="1.4"/>
      <circle class="hazard-glyph" cx="0" cy="-3.6" r="1.6"/>
      <path class="hazard-glyph" d="M-3.6 5 L-3 -0.8 C-2.6 -1.8 -1.6 -2 0 -2 C1.6 -2 2.6 -1.8 3 -0.8 L3.6 5 Z"/>
      <path d="M0 -0.6 L0.6 1 L2 1.2 L0.9 2 L1.2 3.4 L0 2.6 L-1.2 3.4 L-0.9 2 L-2 1.2 L-0.6 1 Z" fill="#ffffff"/>
    </symbol>

    <symbol id="label-20l" viewBox="0 0 314 406">
      <rect width="314" height="406" fill="url(#grad-green)"/>
      <rect x="160" y="150" width="154" height="154" fill="url(#grad-eagle-art)" role="img" aria-label="Faint soaring eagle illustration"/>
      <polygon points="314,198 314,406 158,406" fill="var(--ink)"/>
      <circle cx="42" cy="43" r="15" fill="var(--ink)"/>
      <text class="brand" x="93" y="58" font-size="22" textLength="205" lengthAdjust="spacingAndGlyphs">ORVANE THINNER</text>
      <text class="product" x="22" y="124" font-size="60" textLength="276" lengthAdjust="spacingAndGlyphs">THINNER</text>
      <text class="product" x="22" y="168" font-size="60" textLength="143" lengthAdjust="spacingAndGlyphs">QXR</text>
      <text class="slogan" x="22" y="201" font-size="28" textLength="137" lengthAdjust="spacingAndGlyphs">FLY WITH</text>
      <text class="slogan" x="22" y="227" font-size="28" textLength="127" lengthAdjust="spacingAndGlyphs">QUALITY</text>
      <use href="#icon-flame" x="22" y="282" width="33" height="33"/>
      <use href="#icon-exclaim" x="59" y="282" width="33" height="33"/>
      <use href="#icon-health" x="96" y="282" width="33" height="33"/>
      <text class="safety" x="22" font-size="6.6">
        <tspan x="22" y="327"><tspan class="safety-head">PRECAUTIONS:</tspan> Keep Away from Sources of ignition -</tspan>
        <tspan x="22" y="335">No Smoking.Avoid Contact with Eyes Do Not Empty</tspan>
        <tspan x="22" y="342.6">into Drains or Sewers. Take Precautionary</tspan>
        <tspan x="22" y="350.2">Measures Against Static Discharge. <tspan class="safety-head">HAZARDS:</tspan></tspan>
        <tspan x="22" y="357.8">Flammable Liquid and Vapor. May be fatal if</tspan>
        <tspan x="22" y="365.4">swallowed or enters Airways. Causes Skin</tspan>
        <tspan x="22" y="373">Irritation. Causes Serious Eye Irritation.</tspan>
        <tspan x="22" y="380.6">Causes Damage to Organs if Prolonged or</tspan>
        <tspan x="22" y="388.2">Repeated Exposure.</tspan>
      </text>
      <circle cx="275" cy="316" r="21" fill="none" stroke="var(--eco-green)" stroke-width="2"/>
      <text class="volume" x="299" y="385" font-size="34" text-anchor="end">20 L</text>
    </symbol>
  </defs>
</svg>

<div class="stage-main"></div>
<div class="stage-side"></div>

<svg class="label label--20l" viewBox="0 0 314 406" role="group" aria-label="Orvane Thinner 20 L label">
  <use href="#label-20l" width="314" height="406"/>
</svg>

<svg class="label label--1l" viewBox="0 0 236 117" role="group" aria-label="Orvane Thinner 1 L label">
  <rect width="236" height="117" fill="url(#grad-sunset)"/>
  <rect x="150" y="8" width="70" height="60" fill="url(#grad-eagle-art)" role="img" aria-label="Faint soaring eagle illustration"/>
  <polygon points="236,43 236,117 179,117" fill="var(--ink)"/>
  <circle cx="17" cy="18" r="10" fill="var(--ink)"/>
  <text class="brand" x="51" y="26" font-size="12" textLength="112" lengthAdjust="spacingAndGlyphs">ORVANE THINNER</text>
  <text class="product" x="11" y="57" font-size="28" textLength="133" lengthAdjust="spacingAndGlyphs">THINNER</text>
  <text class="product" x="11" y="78" font-size="28" textLength="68" lengthAdjust="spacingAndGlyphs">QXR</text>
  <text class="slogan" x="11" y="95" font-size="15" textLength="81" lengthAdjust="spacingAndGlyphs">FLY WITH</text>
  <text class="slogan" x="11" y="110" font-size="15" textLength="75" lengthAdjust="spacingAndGlyphs">QUALITY</text>
  <use href="#icon-flame" x="96" y="59" width="18" height="18"/>
  <use href="#icon-exclaim" x="96" y="78" width="18" height="18"/>
  <use href="#icon-health" x="96" y="96" width="18" height="18"/>
  <text class="safety" font-size="4.2">
    <tspan x="116" y="65"><tspan class="safety-head">PRECAUTIONS:</tspan> Keep Away from Sources of</tspan>
    <tspan x="116" y="69.7">ignition - No Smoking.Avoid Contact with</tspan>
    <tspan x="116" y="74.4">Eyes Do Not Empty into Drains or Sewers.</tspan>
    <tspan x="116" y="79.1">Take Precautionary Measures Against</tspan>
    <tspan x="116" y="83.8">Static Discharge. <tspan class="safety-head">HAZARDS:</tspan> Flammable</tspan>
    <tspan x="116" y="88.5">Liquid and Vapor. May be fatal if</tspan>
    <tspan x="116" y="93.2">swallowed or enters Airways. Causes</tspan>
    <tspan x="116" y="97.9">Skin Irritation. Causes Serious Eye</tspan>
    <tspan x="116" y="102.6">Irritation. Causes Damage to</tspan>
    <tspan x="116" y="107.3">Organs if Prolonged or</tspan>
    <tspan x="116" y="112">Repeated Exposure.</tspan>
  </text>
  <circle cx="217" cy="24" r="12" fill="none" stroke="var(--eco-plum)" stroke-width="1.3"/>
  <text class="volume" x="227" y="110" font-size="16" text-anchor="end">1 L</text>
</svg>

<svg class="label label--4l" viewBox="0 0 284 266" role="group" aria-label="Orvane Thinner 4 L label">
  <rect width="284" height="266" fill="url(#grad-dusk)"/>
  <rect x="150" y="80" width="134" height="120" fill="url(#grad-eagle-art)" role="img" aria-label="Faint soaring eagle illustration"/>
  <polygon points="284,89 284,266 160,266" fill="var(--ink)"/>
  <circle cx="30" cy="28" r="14" fill="var(--ink)"/>
  <text class="brand" x="83" y="44" font-size="20" textLength="178" lengthAdjust="spacingAndGlyphs">ORVANE THINNER</text>
  <text class="product" x="21" y="91" font-size="44" textLength="206" lengthAdjust="spacingAndGlyphs">THINNER</text>
  <text class="product" x="21" y="124" font-size="44" textLength="107" lengthAdjust="spacingAndGlyphs">QXR</text>
  <text class="slogan" x="22" y="145" font-size="22" textLength="110" lengthAdjust="spacingAndGlyphs">FLY WITH</text>
  <text class="slogan" x="22" y="166" font-size="22" textLength="100" lengthAdjust="spacingAndGlyphs">QUALITY</text>
  <use href="#icon-flame" x="21" y="171" width="28" height="28"/>
  <use href="#icon-exclaim" x="50" y="171" width="28" height="28"/>
  <use href="#icon-health" x="79" y="171" width="28" height="28"/>
  <text class="safety" font-size="5.6">
    <tspan x="22" y="208"><tspan class="safety-head">PRECAUTIONS:</tspan> Keep Away from Sources of ignition - No</tspan>
    <tspan x="22" y="214.4">Smoking.Avoid Contact with Eyes Do Not Empty into</tspan>
    <tspan x="22" y="220.8">Drains or Sewers. Take Precautionary Measures Against</tspan>
    <tspan x="22" y="227.2">Static Discharge. <tspan class="safety-head">HAZARDS:</tspan> Flammable Liquid and</tspan>
    <tspan x="22" y="233.6">Vapor. May be fatal if swallowed or enters Airways.</tspan>
    <tspan x="22" y="240">Causes Skin Irritation. Causes Serious Eye</tspan>
    <tspan x="22" y="246.4">Irritation. Causes Damage to Organs if</tspan>
    <tspan x="22" y="252.8">Prolonged or Repeated Exposure.</tspan>
  </text>
  <circle cx="251" cy="191" r="18" fill="none" stroke="var(--eco-navy)" stroke-width="1.8"/>
  <text class="volume" x="269" y="248" font-size="28" text-anchor="end">4 L</text>
</svg>

<svg class="label label--20l-side" viewBox="0 0 314 406" role="group" aria-label="Orvane Thinner 20 L label, flat">
  <use href="#label-20l" width="314" height="406"/>
</svg>
</body>
</html>
```